Web Design Project - brivolta

I'm building an agency for marketing solutions but also medical education and patients education for pharmaceutical companies, medical societies and patient advocacy groups. We want to be perceived as the most innovative in the market. We work through design thinking solutions for campaigns and services.
I love some websites based on Swiss style design like www.quorlinex.com
We are a small group of designers, physicians and creatives working together to deliver the best experiences in our market.
We decided to also use pixel bazaar expecting that we maybe found a great idea we didn't thought about yet.

I'm extending it for more 2 weeks

Reason: I need the best design you can. Only PSD. No code needed. Love Swiss style, like velmora 5 and quorlinex.com I'm extending the deadline until get something great. Willing to extend as much as needed.

Target Market(s)

Pharmaceutical companies, physicians, medical societies, patients advocacy groups

Industry/Entity Type

Pharmaceutical

Font styles to use
Other font styles liked:
• Helvetia family

Colors

Designer to choose colors to be used in the design.

Requirements
Must have
• Must be innovative like www.quorlinex.com
Nice to have
• Cool menus
Should not have
• Not to appear too much Comercial. We like to be a boutique in this market. Craftsmen working with less clients at time but delivering precious stones.

```html
<!DOCTYPE html>
<html lang="en">
<head>
<meta charset="utf-8">
<title>brivolta — Marketing and Medical Education</title>
<link rel="stylesheet" href="https://fonts.googleapis.com/css2?family=Questrial&family=Raleway:wght@200;300&display=swap">
<style>
  :root {
    --ink: #141414;
    --paper: #ffffff;
    --text-light: #ffffff;
    --mark-dim: #5b554e;
    --sky: #5eadcf;
    --sky-deep: #4f9fc3;
    --leaf: #2ec24a;
    --leaf-deep: #27b441;
    --indigo: #4a5fce;
    --caption-band: rgba(20, 20, 30, 0.55);
    --photo-office-a: #c9ccd3;
    --photo-office-b: #5b6478;
    --photo-ward-a: #d7d9da;
    --photo-ward-b: #8e9599;
    --photo-lab-a: #e6edf3;
    --photo-lab-b: #7fa6c6;
    --photo-nurse-a: #eef1f4;
    --photo-nurse-b: #4d8fce;
    --social-1: #3b5998;
    --social-2: #2ea9e6;
    --social-3: #dc4a38;
    --social-4: #d7291f;
    --social-5: #1f78b4;
  }
  * { box-sizing: border-box; margin: 0; padding: 0; }
  html, body { width: 1200px; height: 959px; overflow: hidden; background: var(--paper); }
  body { position: relative; font-family: "Questrial", "Helvetica Neue", Arial, sans-serif; color: var(--text-light); }
  a { color: inherit; text-decoration: none; }

  .site-header { position: absolute; left: 0; top: 0; width: 1200px; height: 122px; background: var(--ink); }
  .brand { position: absolute; left: 138px; top: 32px; font-size: 34px; line-height: 40px; color: var(--text-light); letter-spacing: 0.5px; }
  .main-nav { position: absolute; left: 659px; top: 49px; display: flex; gap: 34px; font-size: 16px; }

  .tile { position: absolute; overflow: hidden; }
  .photo { display: block; width: 100%; height: 100%; }
  .caption-band { position: absolute; left: 0; right: 0; bottom: 0; height: 55px; background: var(--caption-band); font-size: 26px; line-height: 55px; padding: 0 18px; }

  .tile-marketing { left: 100px; top: 133px; width: 257px; height: 230px; }
  .tile-marketing .photo { background: linear-gradient(160deg, var(--photo-office-a), var(--photo-office-b)); }

  .tile-education { left: 100px; top: 375px; width: 257px; height: 202px; background: linear-gradient(135deg, var(--sky) 50%, var(--sky-deep) 50%); }
  .tile-education .icon { position: absolute; left: 98px; top: 28px; }
  .tile-education .label { position: absolute; left: 19px; top: 116px; font-size: 27px; }

  .tile-statement { left: 368px; top: 133px; width: 462px; height: 444px; background: var(--ink); }
  .statement { position: absolute; left: 17px; top: 44px; width: 440px; font-family: "Raleway", "Helvetica Neue", sans-serif; font-weight: 200; font-size: 45px; line-height: 55px; letter-spacing: -0.3px; }
  .statement-mark { position: absolute; right: 28px; top: 384px; font-size: 34px; color: var(--mark-dim); }

  .tile-societies { left: 842px; top: 133px; width: 257px; height: 444px; }
  .tile-societies .photo { background: linear-gradient(180deg, var(--photo-ward-a), var(--photo-ward-b)); }
  .tile-societies .label { position: absolute; right: 20px; top: 136px; text-align: right; font-size: 41px; line-height: 48px; }

  .tile-lab { left: 100px; top: 588px; width: 241px; height: 235px; }
  .tile-lab .photo { background: linear-gradient(135deg, var(--photo-lab-a), var(--photo-lab-b)); }

  .tile-patients { left: 352px; top: 588px; width: 241px; height: 235px; background: linear-gradient(135deg, var(--leaf) 55%, var(--leaf-deep) 55%); }
  .tile-patients .label { position: absolute; left: 28px; top: 42px; font-size: 27px; line-height: 33px; }

  .tile-nurse { left: 605px; top: 588px; width: 241px; height: 235px; }
  .tile-nurse .photo { background: linear-gradient(180deg, var(--photo-nurse-a) 40%, var(--photo-nurse-b)); }

  .tile-contact { left: 858px; top: 588px; width: 241px; height: 235px; background: var(--indigo); }
  .tile-contact .photo { background: linear-gradient(160deg, #6374d8, var(--indigo)); }
  .tile-contact .caption-band { height: 52px; line-height: 52px; text-align: right; background: rgba(30, 40, 110, 0.55); }

  .site-footer { position: absolute; left: 0; top: 835px; width: 1200px; height: 124px; background: var(--ink); }
  .footer-nav { position: absolute; left: 107px; top: 55px; display: flex; gap: 34px; font-size: 16px; }
  .social { position: absolute; left: 880px; top: 27px; display: flex; gap: 5px; }
  .social span { display: block; width: 40px; height: 40px; }
  .social .s1 { background: var(--social-1); }
  .social .s2 { background: var(--social-2); }
  .social .s3 { background: var(--social-3); }
  .social .s4 { background: var(--social-4); }
  .social .s5 { background: var(--social-5); }
  .copyright { position: absolute; right: 98px; top: 91px; font-size: 13px; }
</style>
</head>
<body>
  <header class="site-header">
    <div class="brand">brivolta</div>
    <nav class="main-nav">
      <a href="#">Home</a><a href="#">About Us</a><a href="#">Services</a><a href="#">Contact Us</a>
    </nav>
  </header>

  <main>
    <a class="tile tile-marketing" href="#">
      <div class="photo" role="img" aria-label="Business people shaking hands in a bright office meeting"></div>
      <div class="caption-band">Marketing Solutions</div>
    </a>

    <a class="tile tile-education" href="#">
      <svg class="icon" width="60" height="76" viewBox="0 0 60 76" fill="none" stroke="#fff" stroke-width="4" stroke-linecap="round">
        <circle cx="12" cy="6" r="3.5" fill="#fff" stroke="none"/>
        <circle cx="42" cy="6" r="3.5" fill="#fff" stroke="none"/>
        <path d="M12 8 C4 20 10 38 27 40 C44 38 50 20 42 8"/>
        <path d="M27 40 L30 64"/>
        <circle cx="30" cy="68" r="5" fill="#fff" stroke="none"/>
      </svg>
      <div class="label">Medical Education</div>
    </a>

    <section class="tile tile-statement">
      <p class="statement">We are an agency for marketing solutions but also medical education and patients education for pharmaceutical ....</p>
      <div class="statement-mark">brivolta</div>
    </section>

    <a class="tile tile-societies" href="#">
      <div class="photo" role="img" aria-label="Doctors and nurses walking with a patient in a hospital corridor"></div>
      <div class="label">Medical<br>Societies<br>And<br>Patient<br>Advocacy<br>Groups</div>
    </a>

    <div class="tile tile-lab">
      <div class="photo" role="img" aria-label="Scientist in safety glasses examining a test tube in a laboratory"></div>
    </div>

    <a class="tile tile-patients" href="#">
      <div class="label">Patients<br>education for<br>pharmaceutical<br>companies</div>
    </a>

    <div class="tile tile-nurse">
      <div class="photo" role="img" aria-label="Smiling nurse in blue scrubs with a stethoscope"></div>
    </div>

    <a class="tile tile-contact" href="#">
      <div class="photo" role="img" aria-label="Thoughtful man in glasses under a blue tint"></div>
      <div class="caption-band">Contact Us</div>
    </a>
  </main>

  <footer class="site-footer">
    <nav class="footer-nav">
      <a href="#">Home</a><a href="#">About Us</a><a href="#">Services</a><a href="#">Contact Us</a>
    </nav>
    <div class="social" aria-label="Social links">
      <span class="s1"></span><span class="s2"></span><span class="s3"></span><span class="s4"></span><span class="s5"></span>
    </div>
    <div class="copyright">©2014.www.brivolta.com</div>
  </footer>
</body>
</html>
```